KTV Reception Posterboards

We need 3 posterboard designs for an upcoming reception. I will take your designs and have a local printer put them on foam poster board. I'll need the following please 1) Autos Move By Rail and 2) Safety

On the auto board, please include a big, prominent "3/4 of all autos move by rail." Some type of big, bold splash.

Please make sure the KTV logo is on the bottom right corner of each design.

As a side note, our poster boards are about 2 x 3 ft in size.

Target Market(s)

public officials

Industry/Entity Type

Printer

Requirements
Must have
• bold feel for the poster boards
Nice to have
• Include pics.

```html
<!DOCTYPE html>
<html lang="en">
<head>
<meta charset="utf-8">
<title>Safety Investment and Innovations — KTV</title>
<link href="https://fonts.googleapis.com/css2?family=Open+Sans:wght@400;600;700;800&display=swap" rel="stylesheet">
<style>
  :root {
    --navy: #0b0f6e;
    --ink: #333333;
    --paper: #e4e4e6;
    --teal: #4bbdb5;
    --white: #ffffff;
    --photo-teal: #2fa8a8;
    --photo-sky: #8fb4d6;
    --loco-blue: #2f4f86;
  }
  html, body { margin: 0; padding: 0; overflow: hidden; }
  body { width: 800px; height: 1200px; font-family: "Open Sans", Arial, sans-serif; }
  .poster {
    position: relative; width: 800px; height: 1200px;
    background: var(--paper); overflow: hidden; color: var(--ink);
  }
  .title {
    position: absolute; top: 30px; left: 0; width: 800px; margin: 0;
    text-align: center; color: var(--navy);
    font-weight: 800; font-size: 61px; line-height: 63px; letter-spacing: 1px;
  }
  .quote {
    position: absolute; top: 170px; left: 27px; width: 740px; margin: 0;
    font-size: 21.5px; line-height: 31px; text-align: justify; color: #3a3a3a;
  }
  .section-head {
    position: absolute; margin: 0; color: var(--navy); font-weight: 700;
  }
  .since-head { top: 312px; left: 25px; font-size: 25px; }
  .stats {
    position: absolute; top: 356px; left: 25px; margin: 0; padding: 0; list-style: none;
    font-size: 15.5px; line-height: 29.5px;
  }
  .stats li::before {
    content: ""; display: inline-block; width: 7px; height: 7px; border-radius: 50%;
    background: var(--navy); margin: 0 14px 2px 3px; vertical-align: middle;
  }
  .training-photo {
    position: absolute; top: 456px; left: 24px; width: 362px; height: 273px;
    border: 3px solid var(--white);
    background: linear-gradient(180deg, var(--photo-sky) 0%, var(--photo-teal) 35%, #1e7f86 62%, #5a5a4e 100%);
  }
  .training-head { top: 744px; left: 24px; font-size: 25px; }
  .training-copy {
    position: absolute; top: 788px; left: 24px; width: 368px; margin: 0;
    font-size: 15.2px; line-height: 25.5px; text-align: justify;
  }
  .ptc-head { top: 306px; left: 413px; font-size: 21px; letter-spacing: 0.3px; }
  .ptc-copy {
    position: absolute; top: 337px; left: 414px; width: 352px; margin: 0;
    font-size: 15px; line-height: 20.5px; text-align: justify;
  }
  .chart-box {
    position: absolute; top: 528px; left: 414px; width: 345px; height: 220px;
    border: 3px solid var(--white);
  }
  .chart-title {
    position: absolute; top: 10px; left: 0; width: 345px; margin: 0; text-align: center;
    color: var(--navy); font-weight: 700; font-size: 13.6px; line-height: 21px;
  }
  .chart-sub {
    position: absolute; top: 54px; left: 0; width: 345px; margin: 0; text-align: center;
    font-size: 8.5px; font-weight: 600; color: #222;
  }
  .chart-box svg { position: absolute; top: 0; left: 0; }
  .pie-label { font-family: "Open Sans", Arial, sans-serif; font-weight: 700; font-size: 10.5px; fill: #222; }
  .pie-pct { font-family: "Open Sans", Arial, sans-serif; font-weight: 700; font-size: 13px; fill: var(--white); }
  .vs { font-family: "Open Sans", Arial, sans-serif; font-weight: 700; font-size: 30px; fill: #3a3a3a; }
  .hazmat {
    position: absolute; top: 768px; left: 414px; width: 352px; margin: 0;
    font-size: 15.2px; line-height: 24px; text-align: justify;
  }
  .hazmat strong { color: var(--navy); font-size: 22px; font-weight: 800; }
  .locomotive-photo {
    position: absolute; top: 896px; left: 0; width: 800px; height: 304px;
    background: linear-gradient(180deg, var(--paper) 0%, #c9d3df 30%, var(--loco-blue) 62%, #1f2a44 100%);
  }
  .brand {
    position: absolute; top: 905px; left: 652px; margin: 0;
    color: var(--navy); font-weight: 800; font-size: 52px; line-height: 60px; letter-spacing: 1px;
  }
</style>
</head>
<body>
<main class="poster">
  <h1 class="title">SAFETY INVESTMENT<br>AND INNOVATIONS</h1>

  <p class="quote">“Railroads’ annual investments to modernize and improve America’s freight rail network have significantly contributed to freight rail’s strong safety record. There is a direct correlation between the increase in rail network investments and enhanced safety performance.”</p>

  <h2 class="section-head since-head">Since 2000:</h2>
  <ul class="stats">
    <li>The train accident rate fell 38 percent</li>
    <li>The rail employee injury rate fell 47 percent</li>
    <li>The grade crossing collision rate fell 42 percent</li>
  </ul>

  <div class="training-photo" role="img" aria-label="Photo of emergency responders in safety vests training beside a teal tank car"></div>

  <h2 class="section-head training-head">Emergency Response Training</h2>
  <p class="training-copy">Each year, thousands of emergency responders and railroad and shipper employees receive specialized training through individual railroad efforts and industry programs.</p>

  <h2 class="section-head ptc-head">POSITIVE TRAIN CONTROL (PTC)</h2>
  <p class="ptc-copy">Since 2008, freight railroads have worked closely with the federal government and passenger railroads to implement PTC — the largest and most complex safety system in the history of the railroad industry. This cutting-edge technology is designed to automatically stop a train before certain accidents occur. Emergency Response Training Each year, thousands of emergency responders and railroad.</p>

  <section class="chart-box">
    <p class="chart-title">FREIGHT RAIL INVESTS SIX TIMES MORE THAN<br>THE AVERAGE U.S. MANUFACTURER</p>
    <p class="chart-sub">Capital Spending as a Percentage of Revenue</p>
    <svg width="345" height="220" viewBox="0 0 345 220">
      <g class="pie-rail">
        <circle cx="66" cy="137" r="52" fill="var(--navy)"/>
        <path d="M66 137 L66 85 A52 52 0 0 0 17.65 117.86 Z" fill="var(--teal)"/>
        <circle cx="66" cy="137" r="16" fill="var(--white)"/>
        <rect x="57" y="131" width="18" height="10" fill="var(--teal)"/>
        <circle cx="60" cy="143" r="2" fill="var(--teal)"/>
        <circle cx="72" cy="143" r="2" fill="var(--teal)"/>
        <text class="pie-pct" x="25" y="113">19%</text>
        <text class="pie-label" x="66" y="214" text-anchor="middle">Freight Rail</text>
      </g>
      <text class="vs" x="172" y="148" text-anchor="middle">VS.</text>
      <g class="pie-mfg">
        <circle cx="271" cy="137" r="52" fill="var(--navy)"/>
        <path d="M271 137 L271 85 A52 52 0 0 0 261.26 85.92 Z" fill="var(--teal)"/>
        <circle cx="271" cy="137" r="16" fill="var(--white)"/>
        <path d="M262 144 V134 L267 137 V134 L272 137 V128 H276 V144 Z" fill="var(--teal)"/>
        <text class="pie-pct" x="278" y="104">3%</text>
        <text class="pie-label" x="257" y="214" text-anchor="middle">Average U.S. Manufacturer</text>
      </g>
    </svg>
  </section>

  <p class="hazmat">Today, <strong>99.99%</strong> of all hazmat moved by rail reaches its destination without a release caused by an incident. This strong safety record is among the many reasons the federal government requires railroads to transport hazmat.</p>

  <div class="locomotive-photo" role="img" aria-label="Photo of a blue and white freight locomotive pulling red boxcars under a pale sky"></div>

  <p class="brand">KTV</p>
</main>
</body>
</html>
```